Maple Roster Business Card for recruitment company

We are looking for a Business Card Design that incorporates our personal details and our busines name and logo. We are a specialized search consultancy that recruit Property and Construction professionals.
We would like a business card that stands out and is appealing to the Construction and Property industry as well.

Target Market(s)

people in the construction and property industry

Contact Information for Business Card

Business Name and logo

Font styles to use
Serif

Colors
0094D4
00A9DD
6FCCEA
C7EBF8
E9F6FB

Requirements
Must have
• Business name and logo as well as contact details
Should not have
• No photos of us please

```html
<!DOCTYPE html>
<html lang="en">
<head>
<meta charset="utf-8">
<title>Maple Roster — Business Card</title>
<link href="https://fonts.googleapis.com/css2?family=Lora:wght@400;700&display=swap" rel="stylesheet">
<style>
  :root {
    --backdrop: #2b2b2c;
    --blue-strong: #0094d4;
    --blue-bright: #00a9dd;
    --blue-soft: #6fccea;
    --blue-pale: #c7ebf8;
    --blue-mist: #e9f6fb;
    --paper: #ffffff;
    --ink: #2f3a42;
    --white: #ffffff;
  }
  * { margin: 0; padding: 0; box-sizing: border-box; }
  html, body {
    width: 1200px; height: 732px; overflow: hidden;
    background: var(--backdrop);
  }
  .canvas {
    position: relative; width: 1200px; height: 732px;
    font-family: "Lora", Georgia, serif;
  }
  .card {
    position: absolute; top: 242px;
    width: 436px; height: 248px; overflow: hidden;
  }

  /* Wordmark: name plus one plain circle */
  .wordmark {
    position: absolute;
    display: flex; align-items: center; gap: 8px;
    font-family: "Lora", Georgia, serif;
    font-weight: 400; line-height: 1;
    white-space: nowrap;
    color: var(--white);
    transform: translate(-50%, -50%) rotate(-90deg);
  }
  .wordmark__dot {
    flex: none; border-radius: 50%;
    background: var(--white);
  }

  /* Front */
  .card--front {
    left: 144px;
    background: linear-gradient(160deg, var(--paper) 0%, var(--blue-mist) 100%);
  }
  .brand-band {
    position: absolute; left: 0; top: 0;
    width: 116px; height: 100%;
    background: var(--blue-strong);
  }
  .brand-band__rule {
    position: absolute; left: 107px; top: 41px;
    width: 1px; height: 168px;
    background: var(--white);
  }
  .brand-band .wordmark {
    left: 53px; top: 122px;
    font-size: 19px; letter-spacing: 1px;
  }
  .brand-band .wordmark__dot { width: 9px; height: 9px; }

  .details {
    position: absolute; left: 163px; top: 38px;
    color: var(--ink);
  }
  .details__name {
    font-weight: 700; font-size: 19px; line-height: 1;
    color: var(--blue-strong);
  }
  .details__role {
    font-size: 13.5px; line-height: 1; margin-top: 4px;
  }
  .contact {
    list-style: none; margin-top: 40px;
    font-size: 13.5px; line-height: 14.5px;
  }
  .contact__label {
    display: inline-block; width: 21px;
    font-weight: 700; font-size: 12px;
    color: var(--blue-strong);
  }
  .details__location {
    position: absolute; left: 163px; top: 192px;
    font-size: 13.5px; line-height: 1; color: var(--ink);
  }

  /* Back */
  .card--back {
    left: 621px;
    background: linear-gradient(170deg, var(--blue-bright) 0%, var(--blue-strong) 100%);
  }
  .card--back .wordmark {
    left: 403px; top: 123px;
    font-size: 25px; letter-spacing: 1.5px;
  }
  .card--back .wordmark__dot { width: 11px; height: 11px; }
</style>
</head>
<body>
<main class="canvas">
  <section class="card card--front" aria-label="Business card front">
    <div class="brand-band">
      <span class="wordmark"><span>MAPLE ROSTER</span><span class="wordmark__dot"></span></span>
      <span class="brand-band__rule"></span>
    </div>
    <div class="details">
      <h1 class="details__name">Clara Whitfield</h1>
      <p class="details__role">Director&nbsp;|&nbsp;Senior Search Consultant</p>
      <ul class="contact">
        <li><span class="contact__label">T:</span> +64 21 480 2291</li>
        <li><span class="contact__label">E:</span> clara@mapleroster.nz</li>
        <li><span class="contact__label">W:</span> www.mapleroster.nz</li>
      </ul>
    </div>
    <p class="details__location">Auckland, New Zealand</p>
  </section>

  <section class="card card--back" aria-label="Business card back">
    <span class="wordmark"><span>MAPLE ROSTER</span><span class="wordmark__dot"></span></span>
  </section>
</main>
</body>
</html>
```